Business card for Luxury Portable Restroom Trailer company

We are a Luxury Portable Restroom Trailer Company Called FALCRIDGE HIRES. Based in Orange County California. We provide portable restroom trailers for events, such as, Weddings, Concerts, Charity events, Sporting events, Tournaments, Corporate events, ect. We rent and Sell the Luxury restrooms. Our colors are white, grey, and Orange. As you will see in the logo we uploaded.
There are 2 people in the company so the names and titles will change for the 3 people but card will remain the same. Here is the information for each Person: Dwight Penner CFO 555 318-0476
next Person: Leon Marchetti VP 555 318-0476
Next Person: Owen Marchetti CEO 555 318-0476
Information to include on the card: Luxury Restroom Trailers Rental and Sales. Weddings, Concerts, Charity, Sporting and Corp. Events.

```html
<!DOCTYPE html>
<html lang="en">
<head>
<meta charset="utf-8">
<title>Falcridge Hires – Business Card</title>
<link href="https://fonts.googleapis.com/css2?family=Montserrat:wght@400;500;800&display=swap" rel="stylesheet">
<style>
  :root {
    --orange: #f26f24;
    --grey: #58595b;
    --ink: #1c1c1c;
    --white: #ffffff;
    --backdrop: #2b2b2b;
  }
  * { margin: 0; padding: 0; box-sizing: border-box; }
  html, body {
    width: 1200px; height: 880px; overflow: hidden;
    background: var(--backdrop);
    font-family: "Montserrat", sans-serif;
  }
  .canvas { position: relative; width: 1200px; height: 880px; }
  .card {
    position: absolute; width: 560px; height: 320px; overflow: hidden;
    box-shadow: 0 10px 30px rgba(0,0,0,.45);
  }
  /* Front */
  .card--front { left: 30px; top: 90px; background: var(--orange); color: var(--white); }
  .brand {
    font-weight: 800; text-transform: uppercase; letter-spacing: 2px; line-height: 1;
    display: flex; align-items: center; gap: 12px;
  }
  .brand__dot { display: block; width: 14px; height: 14px; }
  .card--front .brand { position: absolute; left: 0; right: 0; top: 96px; justify-content: center; font-size: 42px; }
  .card--front .brand__dot { background: var(--white); }
  .services {
    position: absolute; left: 0; right: 0; top: 200px; text-align: center;
    font-size: 15px; font-weight: 500; line-height: 1.75; list-style: none;
  }
  .services li { display: inline; }
  .services li::before { content: "\25CF"; margin: 0 6px 0 10px; font-size: 11px; }
  /* Back */
  .card--back { left: 610px; top: 470px; background: var(--white); }
  .card--back .brand {
    position: absolute; right: 28px; top: 32px; font-size: 24px; color: var(--grey);
  }
  .card--back .brand__dot { background: var(--grey); width: 10px; height: 10px; }
  .swoosh { position: absolute; inset: 0; }
  .team { position: absolute; left: 36px; top: 84px; list-style: none; }
  .member + .member { margin-top: 6px; }
  .member__name {
    font-weight: 800; font-size: 15px; line-height: 18px; color: var(--orange);
    text-transform: uppercase; letter-spacing: .5px;
  }
  .member__title { font-size: 13px; line-height: 16px; color: var(--ink); margin-top: 2px; }
  .member__phone {
    font-size: 13px; line-height: 16px; color: var(--ink);
    display: flex; align-items: center; gap: 6px; margin-top: 2px;
  }
  .member__phone svg { width: 13px; height: 13px; fill: var(--orange); }
</style>
</head>
<body>
<main class="canvas">
  <section class="card card--front">
    <div class="brand"><span class="brand__dot"></span>Falcridge Hires</div>
    <ul class="services">
      <li>Luxury Restroom Trailers Rental and Sales</li><br>
      <li>Weddings</li><li>Concerts</li><li>Charity</li><li>Sporting and Corp</li><li>Events</li>
    </ul>
  </section>

  <section class="card card--back">
    <svg class="swoosh" viewBox="0 0 560 320" aria-hidden="true">
      <path d="M0,320 L0,306 C270,306 350,252 432,176 C482,134 522,114 560,104 L560,320 Z" fill="var(--orange)"/>
      <path d="M0,284 C260,284 340,230 415,154 L423,163 C346,242 266,297 0,297 Z" fill="var(--grey)"/>
      <circle cx="472" cy="132" r="62" fill="var(--white)" stroke="var(--orange)" stroke-width="9"/>
    </svg>
    <div class="brand"><span class="brand__dot"></span>Falcridge Hires</div>
    <ul class="team">
      <li class="member">
        <div class="member__name">Dwight Penner</div>
        <div class="member__title">CFO</div>
        <div class="member__phone"><svg viewBox="0 0 24 24" aria-hidden="true"><path d="M6.6 10.8a15.2 15.2 0 0 0 6.6 6.6l2.2-2.2a1 1 0 0 1 1-.25 11.4 11.4 0 0 0 3.6.57 1 1 0 0 1 1 1V20a1 1 0 0 1-1 1A17 17 0 0 1 3 4a1 1 0 0 1 1-1h3.5a1 1 0 0 1 1 1c0 1.25.2 2.45.57 3.57a1 1 0 0 1-.25 1z"/></svg>555 318-0476</div>
      </li>
      <li class="member">
        <div class="member__name">Leon Marchetti</div>
        <div class="member__title">VP</div>
        <div class="member__phone"><svg viewBox="0 0 24 24" aria-hidden="true"><path d="M6.6 10.8a15.2 15.2 0 0 0 6.6 6.6l2.2-2.2a1 1 0 0 1 1-.25 11.4 11.4 0 0 0 3.6.57 1 1 0 0 1 1 1V20a1 1 0 0 1-1 1A17 17 0 0 1 3 4a1 1 0 0 1 1-1h3.5a1 1 0 0 1 1 1c0 1.25.2 2.45.57 3.57a1 1 0 0 1-.25 1z"/></svg>555 318-0476</div>
      </li>
      <li class="member">
        <div class="member__name">Owen Marchetti</div>
        <div class="member__title">CEO</div>
        <div class="member__phone"><svg viewBox="0 0 24 24" aria-hidden="true"><path d="M6.6 10.8a15.2 15.2 0 0 0 6.6 6.6l2.2-2.2a1 1 0 0 1 1-.25 11.4 11.4 0 0 0 3.6.57 1 1 0 0 1 1 1V20a1 1 0 0 1-1 1A17 17 0 0 1 3 4a1 1 0 0 1 1-1h3.5a1 1 0 0 1 1 1c0 1.25.2 2.45.57 3.57a1 1 0 0 1-.25 1z"/></svg>555 318-0476</div>
      </li>
    </ul>
  </section>
</main>
</body>
</html>
```